Quick Straightforward Billboard Redesign

- Design billboard sized for 10 foot' x 36' foot width live area size and please include bleeds 6" around all sides
- Exact blue color match is imperative in headline, logo, phone number bubble or wherever used. C-83 / M-45 / Y-1 / K-0-
- What I hope to illustrate is that our company offers the best porch screening in the area area, in regards to quality, expertise, durability, storms proof, but we do not build screen porches.
- Current board is attached below from previous designer, and as you can see sizing was off, white space on edges make it appear to be sized incorrectly.
- I also attached my own little mock up idea well well if it helps, favorite image, logo, headline, etc and ideas perhaps on expanding or making this better?

Thanks so much!

Target Market(s)

Drivers and passengers, Southeastern NC, are of immense new construction and high end homes.

Industry/Entity Type

Construction

Colors
0054AA
0677BA
7BADD7
CADEEF
E8F1F8

Requirements
Must have
• Blue color matching
Nice to have
• Design spins or other thoughts on my little mock up

```html
<!DOCTYPE html>
<html lang="en">
<head>
<meta charset="utf-8">
<title>Harborside Screens — Billboard</title>
<link href="https://fonts.googleapis.com/css2?family=Bebas+Neue&family=Oswald:wght@500&display=swap" rel="stylesheet">
<style>
  :root {
    --page-bg: #e9eaec;
    --board-white: #ffffff;
    --brand-blue: #0f68b3;
    --accent-blue: #1878bf;
    --sky-blue: #22bfea;
    --band-blue: #1e7fc2;
    --band-teal: #1f9f9e;
    --band-green: #23b464;
    --rule: #7fc3e0;
  }
  html, body {
    margin: 0;
    padding: 0;
    width: 1200px;
    height: 420px;
    overflow: hidden;
    background: var(--page-bg);
  }
  .billboard {
    position: absolute;
    left: 30px;
    top: 52px;
    width: 1140px;
    height: 316px;
    display: block;
  }
  .board-face { fill: var(--board-white); }
  .brand-square { fill: var(--sky-blue); }
  .brand-name {
    font-family: "Bebas Neue", "Oswald", sans-serif;
    font-size: 83px;
    fill: var(--brand-blue);
  }
  .divider { stroke: var(--rule); stroke-width: 1; }
  .web-address, .call-line {
    font-family: "Oswald", sans-serif;
    font-weight: 500;
    fill: var(--accent-blue);
  }
  .web-address { font-size: 50px; }
  .call-line { font-size: 66px; }
  .headline {
    font-family: "Bebas Neue", "Oswald", sans-serif;
    font-size: 90px;
    fill: var(--board-white);
  }
  .phone-glyph { fill: none; stroke: var(--board-white); stroke-width: 3; stroke-linecap: round; stroke-linejoin: round; }
</style>
</head>
<body>
<svg class="billboard" viewBox="0 0 1140 316" xmlns="http://www.w3.org/2000/svg" aria-label="Harborside Screens billboard">
  <defs>
    <linearGradient id="band-gradient" x1="0" y1="0" x2="1" y2="0">
      <stop offset="0" stop-color="var(--band-blue)"/>
      <stop offset="0.5" stop-color="var(--band-teal)"/>
      <stop offset="1" stop-color="var(--band-green)"/>
    </linearGradient>
    <linearGradient id="bubble-gradient" x1="0" y1="1" x2="1" y2="0">
      <stop offset="0" stop-color="var(--band-green)"/>
      <stop offset="1" stop-color="var(--band-teal)"/>
    </linearGradient>
  </defs>

  <rect class="board-face" x="0" y="0" width="1140" height="316"/>

  <!-- brand block -->
  <rect class="brand-square" x="42" y="60" width="136" height="136"/>
  <text class="brand-name" x="205" y="109" textLength="278" lengthAdjust="spacingAndGlyphs">HARBORSIDE</text>
  <text class="brand-name" x="205" y="191" textLength="278" lengthAdjust="spacingAndGlyphs">SCREENS</text>
  <line class="divider" x1="42" y1="217.5" x2="483" y2="217.5"/>
  <text class="web-address" x="39" y="283" textLength="443" lengthAdjust="spacingAndGlyphs">www.harborsidescreens.com</text>

  <!-- headline band -->
  <polygon points="556,30 1140,30 1140,217 517,217 517,85" fill="url(#band-gradient)"/>
  <text class="headline" x="565" y="116" textLength="537" lengthAdjust="spacingAndGlyphs">SCREEN YOUR PORCH.</text>
  <text class="headline" x="565" y="194" textLength="537" lengthAdjust="spacingAndGlyphs">BUILT FOR THE COAST.</text>

  <!-- call line -->
  <circle cx="589" cy="265" r="25" fill="url(#bubble-gradient)"/>
  <path class="phone-glyph" d="M579,255 q-3,3 0,9 q5,9 13,13 q6,3 9,0 l2,-3 l-6,-5 l-3,3 q-6,-3 -9,-9 l3,-3 l-5,-6 z"/>
  <path class="phone-glyph" d="M591,255 q6,1 7,7 M592,250 q10,2 11,12" stroke-width="2"/>
  <text class="call-line" x="634" y="290" textLength="448" lengthAdjust="spacingAndGlyphs">Call us 910.555.0142</text>
</svg>
</body>
</html>
```